Brellwick Partners, LLC Stationary

Brellwick Partners, LLC is a new financial planning and consulting company. We are looking for designs on business cards, letterhead, envelopes, and anything else that would be useful. Our preference for business card design is two sided. We are looking for a professional and clean look with incorporating the logo and patriotic feel. Thank you to all who participate and good luck!

```html
<!DOCTYPE html>
<html lang="en">
<head>
<meta charset="utf-8">
<title>Brellwick Partners, LLC — Business Card</title>
<link href="https://fonts.googleapis.com/css2?family=Arimo:wght@400;700&display=swap" rel="stylesheet">
<style>
  :root {
    --navy: #1d3f6e;
    --navy-deep: #173458;
    --red: #c4222a;
    --red-deep: #a81b22;
    --white: #ffffff;
    --paper: #f1f1f1;
    --backdrop: #2f2f31;
  }
  * { margin: 0; padding: 0; box-sizing: border-box; }
  html, body { width: 1200px; height: 950px; overflow: hidden; }
  body {
    background: var(--backdrop);
    font-family: "Arimo", Arial, sans-serif;
    position: relative;
  }
  .card {
    position: absolute;
    left: 250px;
    width: 700px;
    height: 400px;
    overflow: hidden;
    box-shadow: 0 10px 30px rgba(0,0,0,.45);
  }
  .card--back { top: 55px; background: linear-gradient(135deg, var(--navy) 0%, var(--navy-deep) 100%); }
  .card--front { top: 495px; background: linear-gradient(160deg, var(--white) 40%, var(--paper) 100%); }

  .card__shapes { position: absolute; inset: 0; }

  .brand {
    position: absolute;
    display: flex;
    align-items: center;
    gap: 12px;
    font-weight: 700;
    letter-spacing: .04em;
    text-transform: uppercase;
  }
  .brand__dot { width: 14px; height: 14px; border-radius: 50%; flex: none; }
  .card--back .brand { left: 190px; top: 160px; color: var(--white); font-size: 30px; }
  .card--back .brand__dot { background: var(--white); }
  .card--front .brand { left: 390px; top: 150px; color: var(--navy); font-size: 24px; line-height: 1.15; }
  .card--front .brand__dot { background: var(--red); }

  .back__web {
    position: absolute;
    left: 216px; top: 232px;
    color: var(--white);
    font-size: 17px;
    letter-spacing: .2em;
  }

  .contact {
    position: absolute;
    left: 36px; top: 70px;
    color: var(--white);
  }
  .contact__name { font-size: 22px; font-weight: 700; }
  .contact__role { font-size: 15px; margin-top: 4px; }
  .contact__address { font-size: 15px; line-height: 1.35; margin-top: 26px; }
  .contact__list { list-style: none; margin-top: 4px; font-size: 15px; line-height: 1.45; }
  .contact__list li { display: flex; align-items: center; gap: 8px; }
  .contact__list svg { width: 13px; height: 13px; fill: var(--white); flex: none; }
</style>
</head>
<body>

<section class="card card--back" aria-label="Business card, reverse side">
  <div class="brand"><span class="brand__dot"></span>Brellwick Partners, LLC</div>
  <div class="back__web">www.brellwick.com</div>
</section>

<section class="card card--front" aria-label="Business card, front side">
  <svg class="card__shapes" viewBox="0 0 700 400" preserveAspectRatio="none" aria-hidden="true">
    <polygon points="250,0 300,0 390,400 330,400" fill="var(--navy)"/>
    <polygon points="0,0 250,0 330,400 0,400" fill="var(--red)"/>
    <polygon points="232,0 270,0 256,14" fill="var(--red-deep)"/>
  </svg>

  <div class="contact">
    <div class="contact__name">Marcus Hale</div>
    <div class="contact__role">President</div>
    <div class="contact__address">1420 Harborview Lane<br>Ridgefield, CT 06877</div>
    <ul class="contact__list">
      <li><svg viewBox="0 0 16 16"><path d="M3 1l3 3-1.5 2a9 9 0 0 0 5.5 5.5L12 10l3 3-2 2C6 15 1 10 1 3z"/></svg>203 555 0148</li>
      <li><svg viewBox="0 0 16 16"><rect x="4" y="1" width="8" height="5"/><rect x="1" y="6" width="14" height="6" rx="1"/><rect x="4" y="10" width="8" height="5"/></svg>203 555 0192</li>
      <li><svg viewBox="0 0 16 16"><path d="M1 3h14v10H1z M1 3l7 6 7-6" stroke="var(--red)" stroke-width="1"/></svg>marcus@brellwick.com</li>
      <li><svg viewBox="0 0 16 16"><circle cx="8" cy="8" r="7"/></svg>www.brellwick.com</li>
    </ul>
  </div>

  <div class="brand"><span class="brand__dot"></span>Brellwick<br>Partners, LLC</div>
</section>

</body>
</html>
```